International business needs business cards

Our company, DRV Ventures Inc. is in the business of supplying a range construction products with particular emphasis on CEMENT. We have developed our own brand - TORVAN SUPPLIES - with which to infiltrate the market. We are launching our brand of cement (TORVAN Type IS Cement) into the Caribbean which is unlike anything this market has ever seen. A monopoly has existed here for the past 60-odd years and the market has now opened to allow the importation of other brands and consumers are anxious and ready for change/improvement. We are very excited to be launching and want to make a great first impression. We will be conducting workshops and seminars (from government level to the hardware store owners) and we want our business card to give us the strong, confident introduction that we need.

Target Market(s)

construction; builders; engineers; home owners

Industry/Entity Type

Construction

Contact Information for Business Card

Marisol Depree
CEO
cell # 1 555 4180736
Ground floor,Lindell Plaza Suite 2734
George Town,Grand Cayman
Cayman Islands,KY1-4823
EMAIL: m.depree@drvventuresinc.example
web site drvventuresinc.example

COMPANY: skype info drv.ventures.example

second card
Yvette Brannock-Depree
CFO
CELL# 1 555 607 3941
George Town,Grand Cayman
Cayman Islands,KY1-4823
EMAIL: y.brannockdepree@drvventuresinc.example
website drvventuresinc.example

Requirements
Must have
• Business cards must display BOTH logos - DRV is the company and TORVAN is the brand.

```html
<!DOCTYPE html>
<html lang="en">
<head>
<meta charset="utf-8">
<title>DRV Ventures Inc. — Business Card</title>
<link rel="stylesheet" href="https://fonts.googleapis.com/css2?family=Open+Sans:wght@400;600;700;800&display=swap">
<style>
  :root {
    --maroon: #6d1216;
    --maroon-text: #7a1518;
    --ink: #111111;
    --body-grey: #5e5e5e;
    --card-white: #f4f4f4;
    --backdrop: #9b9b9b;
    --on-maroon: #e9e2e2;
  }
  * { margin: 0; padding: 0; box-sizing: border-box; }
  html, body {
    width: 1105px; height: 1200px; overflow: hidden;
    background: var(--backdrop);
    font-family: "Open Sans", Arial, sans-serif;
  }
  .canvas { position: relative; width: 1105px; height: 1200px; }

  .card {
    position: absolute; left: 182px; width: 746px; height: 424px;
  }
  .card--front { top: 120px; background: var(--card-white); }
  .card--back { top: 637px; background: var(--maroon); }

  /* company mark */
  .company-mark { position: absolute; left: 442px; top: 28px; display: flex; align-items: center; gap: 14px; }
  .company-mark__square { width: 108px; height: 108px; background: var(--maroon); }
  .company-mark__name { color: var(--ink); font-weight: 800; line-height: 1; }
  .company-mark__name .big { display: block; font-size: 74px; letter-spacing: 1px; }
  .company-mark__name .small { display: block; font-size: 21px; margin-top: 6px; letter-spacing: .5px; }

  /* name block */
  .name-tab { position: absolute; left: 0; top: 231px; width: 11px; height: 52px; background: var(--maroon); }
  .person-name { position: absolute; left: 29px; top: 224px; font-size: 26px; font-weight: 600; color: var(--maroon-text); }
  .person-title { position: absolute; left: 29px; top: 258px; font-size: 19px; color: var(--ink); }
  .divider { position: absolute; left: 73px; right: 27px; top: 279px; height: 2px; background: var(--maroon); }

  .address { position: absolute; left: 29px; top: 294px; font-size: 19px; line-height: 27.5px; color: var(--body-grey); }
  .contacts { position: absolute; right: 27px; top: 322px; font-size: 19px; line-height: 27.5px; color: var(--body-grey); text-align: right; }
  .contacts .label { color: var(--maroon-text); font-weight: 700; }

  /* brand mark on reverse */
  .brand-mark { position: absolute; left: 0; right: 0; top: 150px; display: flex; justify-content: center; align-items: center; gap: 18px; }
  .brand-mark__circle { width: 60px; height: 60px; border-radius: 50%; border: 4px solid var(--on-maroon); }
  .brand-mark__name { font-size: 64px; font-weight: 700; color: var(--on-maroon); letter-spacing: 4px; line-height: 1; }
  .back-url { position: absolute; left: 0; right: 0; top: 374px; text-align: center; font-size: 19px; color: var(--on-maroon); }
</style>
</head>
<body>
<main class="canvas">
  <section class="card card--front" aria-label="Card front">
    <div class="company-mark">
      <div class="company-mark__square"></div>
      <div class="company-mark__name"><span class="big">DRV</span><span class="small">VENTURES INC.</span></div>
    </div>

    <div class="name-tab"></div>
    <h1 class="person-name">Marisol Depree</h1>
    <p class="person-title">CEO</p>
    <div class="divider"></div>

    <address class="address" style="font-style:normal">
      Ground floor<br>
      Lindell Plaza Suite 2734<br>
      George Town,Grand Cayman<br>
      Cayman Islands,KY1-4823
    </address>

    <div class="contacts">
      <span class="label">Mobile:</span>1 555 4180736<br>
      m.depree@drvventuresinc.example<br>
      www.drvventuresinc.example
    </div>
  </section>

  <section class="card card--back" aria-label="Card back">
    <div class="brand-mark">
      <div class="brand-mark__circle"></div>
      <div class="brand-mark__name">TORVAN</div>
    </div>
    <p class="back-url">www.drvventuresinc.example</p>
  </section>
</main>
</body>
</html>
```